Corporate Travel Technology Company needs new Business Card design

We need a new business card design to reflect our re-branded company. Our company is called tolven (pronounced tolvenn) and we provide Business Intelligence and Smart Corporate Journeys solutions for the corporate travel industry. Our multinational customers use our solutions to manage large travel budgets and frequent travellers, as well as to save money and reduce risk. We'd like to see designs that use the blue and green palette as well as our corporate logo (attached below). The design should communicate innovation, insight, forward thinking, contemporary, trusted.

Target Market(s)

Large multinational corporates and Travel Agencies.

Industry/Entity Type

Business

Contact Information for Business Card

Rosalind Mercer
Chief Executive
tolven
Phone number - +61 (0)2 8134 2907
Email address - rosalind.mercer@tolven-example.com
Mobile number - +61 (0)438 516 702
www.tolven-example.com

Font styles to use
Other font styles liked:
• Please use font as close to corporate logo as possible

Colors
0255a3
0393ce
00a990
33b8a4
33a6d7
3176b5

Requirements
Must have
• Please include the words;
• Smart Corporate Journeys
• Clearer Spend Decisions for Global Teams
• Use corporate logo - although icon can be stylised if needed

```html
<!DOCTYPE html>
<html lang="en">
<head>
<meta charset="utf-8">
<title>tolven Business Card</title>
<link rel="stylesheet" href="https://fonts.googleapis.com/css2?family=Open+Sans:ital,wght@0,400;0,600;1,400&display=swap">
<style>
  :root {
    --page-bg: #8a8b8c;
    --card-white: #ffffff;
    --slate-green: #475e5b;
    --brand-blue: #00aeef;
    --text-dark: #3f4f4d;
    --text-light: #ffffff;
  }
  * { box-sizing: border-box; margin: 0; padding: 0; }
  html, body {
    width: 1105px;
    height: 1200px;
    overflow: hidden;
    background: var(--page-bg);
    font-family: "Open Sans", Arial, sans-serif;
  }
  .canvas {
    position: relative;
    width: 1105px;
    height: 1200px;
  }
  .card {
    position: absolute;
    left: 180px;
    width: 745px;
    height: 427px;
    overflow: hidden;
  }
  .card--front { top: 118px; background: var(--card-white); }
  .card--back { top: 638px; background: var(--slate-green); }

  .side-panel {
    position: absolute;
    left: 0;
    top: 0;
    width: 300px;
    height: 100%;
    background: var(--slate-green);
  }
  .side-band {
    position: absolute;
    left: 300px;
    top: 0;
    width: 22px;
    height: 100%;
    background: var(--brand-blue);
  }

  .wordmark {
    position: absolute;
    left: 0;
    top: 178px;
    width: 300px;
    text-align: center;
    font-size: 56px;
    font-weight: 400;
    color: var(--text-light);
    line-height: 1;
  }

  .contact {
    position: absolute;
    right: 36px;
    top: 182px;
    text-align: right;
  }
  .contact__name {
    font-size: 33px;
    font-weight: 600;
    color: var(--brand-blue);
    line-height: 1.15;
  }
  .contact__role {
    font-size: 25px;
    color: var(--text-dark);
    line-height: 1.3;
  }
  .contact__email {
    font-size: 17px;
    font-style: italic;
    color: var(--text-dark);
    margin-top: 4px;
  }
  .contact__lines {
    list-style: none;
    margin-top: 30px;
  }
  .contact__line {
    display: flex;
    justify-content: flex-end;
    align-items: center;
    gap: 10px;
    font-size: 17px;
    color: var(--text-dark);
    line-height: 30px;
  }
  .contact__icon { width: 18px; height: 18px; flex: none; }

  .back-name {
    position: absolute;
    left: 0;
    right: 0;
    top: 150px;
    text-align: center;
    font-size: 72px;
    font-weight: 400;
    color: var(--brand-blue);
    line-height: 1;
  }
  .tagline {
    position: absolute;
    left: 0;
    right: 0;
    top: 357px;
    text-align: center;
    font-size: 20px;
    font-style: italic;
    color: var(--text-light);
  }
  .tagline__divider {
    display: inline-block;
    width: 2px;
    height: 22px;
    background: var(--brand-blue);
    margin: 0 8px;
    vertical-align: -4px;
  }
</style>
</head>
<body>
<main class="canvas">

  <section class="card card--front" aria-label="Business card front">
    <div class="side-panel"></div>
    <div class="side-band"></div>

    <div class="wordmark">tolven</div>

    <div class="contact">
      <p class="contact__name">Rosalind Mercer</p>
      <p class="contact__role">Chief Executive</p>
      <p class="contact__email">rosalind.mercer@tolven-example.com</p>
      <ul class="contact__lines">
        <li class="contact__line">
          <span>+61 (0)2 8134 2907</span>
          <svg class="contact__icon" viewBox="0 0 24 24" aria-label="Phone"><path fill="var(--brand-blue)" d="M6.6 10.8a15 15 0 0 0 6.6 6.6l2.2-2.2c.3-.3.7-.4 1-.2 1.1.4 2.3.6 3.6.6.6 0 1 .4 1 1V20c0 .6-.4 1-1 1A17 17 0 0 1 3 4c0-.6.4-1 1-1h3.5c.6 0 1 .4 1 1 0 1.3.2 2.5.6 3.6.1.3 0 .7-.2 1z"/></svg>
        </li>
        <li class="contact__line">
          <span>+61 (0)438 516 702</span>
          <svg class="contact__icon" viewBox="0 0 24 24" aria-label="Mobile"><rect x="6" y="2" width="12" height="20" rx="2" fill="none" stroke="var(--brand-blue)" stroke-width="2"/><circle cx="12" cy="18.5" r="1.2" fill="var(--brand-blue)"/></svg>
        </li>
        <li class="contact__line">
          <span>www.tolven-example.com</span>
          <svg class="contact__icon" viewBox="0 0 24 24" aria-label="Website"><circle cx="12" cy="12" r="10" fill="var(--brand-blue)"/><ellipse cx="12" cy="12" rx="4" ry="10" fill="none" stroke="#fff" stroke-width="1.4"/><line x1="2" y1="12" x2="22" y2="12" stroke="#fff" stroke-width="1.4"/></svg>
        </li>
      </ul>
    </div>
  </section>

  <section class="card card--back" aria-label="Business card back">
    <div class="back-name">tolven</div>
    <p class="tagline">Smart Corporate Journeys<span class="tagline__divider"></span>Clearer Spend Decisions for Global Teams</p>
  </section>

</main>
</body>
</html>
```